Business Card for beauty technology startup

Design Glimora Business Card for a Beauty, based on the website identity and colors (https://www.glimora-example.com).
Glimora is a beauty tech startup that gathers helpful product info for beauty lovers and consumers (such as availability on stores, price range and product reviews) for makeup products. The card design must be young, colorful but clean, and very modern.

Target Market(s)

woman, 15-35

Industry/Entity Type

Cosmetics

Contact Information for Business Card

Full Name, address, phone

Font styles to use
Other font styles liked:
• Advent Pro

Colors
e34297
86cfc6
ffffff
5c5c5c
e8e8e8
e667a6
b2b2b2

Requirements
Must have
• One full colored side with a creative design and another with card info
• Use Color palette: #95C5C5 and/or #D38AA5
• Use fonts: Advent Pro
• Use website identity: https://www.glimora-example.com
Nice to have
• If needed extra font: Roboto

```html
<!DOCTYPE html>
<html lang="en">
<head>
<meta charset="utf-8">
<title>Glimora Business Card</title>
<link rel="stylesheet" href="https://fonts.googleapis.com/css2?family=Advent+Pro:wght@300;400&family=Montserrat:wght@400;500&family=Roboto:wght@500&display=swap">
<style>
  :root {
    --page-bg: #e8e8e8;
    --card-white: #ffffff;
    --brand-pink: #be8397;
    --brand-plum: #47303b;
    --text-dark: #4a3b43;
    --shadow: rgba(0, 0, 0, 0.22);
  }
  * { box-sizing: border-box; margin: 0; padding: 0; }
  html, body {
    width: 1200px; height: 1155px; overflow: hidden;
    background: var(--page-bg);
  }
  .card {
    position: absolute; left: 218px; width: 758px; height: 434px;
    border-radius: 32px; overflow: hidden;
    box-shadow: 0 4px 10px var(--shadow);
  }
  .card-front { top: 134px; background: var(--brand-pink); }
  .card-back { top: 596px; background: var(--card-white); }

  .front-wordmark {
    position: absolute; left: 0; right: 0; top: 160px;
    text-align: center; color: var(--card-white);
    font-family: "Advent Pro", sans-serif; font-weight: 300;
    font-size: 96px; line-height: 1; letter-spacing: 4px;
  }
  .social-row {
    position: absolute; left: 310px; top: 373px;
    display: flex; gap: 13px;
  }
  .social-dot {
    width: 28px; height: 28px; border-radius: 50%;
    background: var(--card-white);
  }

  .back-brand {
    position: absolute; left: 71px; top: 178px;
    display: flex; align-items: center; gap: 26px;
  }
  .brand-circle {
    width: 80px; height: 80px; border-radius: 50%;
    border: 2px solid var(--brand-pink);
  }
  .brand-name {
    font-family: "Advent Pro", sans-serif; font-weight: 300;
    font-size: 58px; letter-spacing: 5px; color: var(--brand-pink);
    line-height: 1;
  }
  .divider {
    position: absolute; left: 436px; top: 120px;
    width: 2px; height: 200px; background: var(--brand-pink);
  }
  .contact {
    position: absolute; left: 472px; top: 116px;
    font-family: "Montserrat", sans-serif; color: var(--text-dark);
    white-space: nowrap;
  }
  .contact-name {
    font-family: "Roboto", sans-serif; font-weight: 500;
    font-size: 26px; letter-spacing: 0.5px; color: var(--brand-pink);
  }
  .contact-role { font-size: 14px; margin-top: 4px; letter-spacing: 0.5px; }
  .contact-address { font-size: 19px; line-height: 28px; margin-top: 10px; }
  .contact-list { list-style: none; margin-top: 8px; }
  .contact-list li {
    display: flex; align-items: center; gap: 18px;
    font-size: 18px; line-height: 28px;
  }
  .contact-icon { width: 13px; height: 13px; flex: none; }
  .bottom-band {
    position: absolute; left: 0; bottom: 0; width: 100%; height: 56px;
    background: linear-gradient(90deg, var(--brand-plum) 0%, var(--brand-pink) 45%, var(--brand-pink) 70%, var(--brand-plum) 100%);
  }
</style>
</head>
<body>
  <section class="card card-front">
    <div class="front-wordmark">Glimora</div>
    <div class="social-row">
      <span class="social-dot"></span>
      <span class="social-dot"></span>
      <span class="social-dot"></span>
      <span class="social-dot"></span>
    </div>
  </section>

  <section class="card card-back">
    <div class="back-brand">
      <span class="brand-circle"></span>
      <span class="brand-name">GLIMORA</span>
    </div>

    <div class="divider"></div>

    <div class="contact">
      <p class="contact-name">MIRA TALVEN</p>
      <p class="contact-role">OWNER</p>
      <p class="contact-address">48 Palm Row<br>Harbor, FL 30412</p>
      <ul class="contact-list">
        <li>
          <svg class="contact-icon" viewBox="0 0 12 12"><path d="M3 1 L5 3.5 L4 5 C4.6 6.4 5.6 7.4 7 8 L8.5 7 L11 9 L10 11 C5.5 11 1 6.5 1 2 Z" fill="var(--brand-pink)"/></svg>
          <span>555.014.2290</span>
        </li>
        <li>
          <svg class="contact-icon" viewBox="0 0 12 12"><rect x="0.8" y="2.3" width="10.4" height="7.4" fill="none" stroke="var(--brand-pink)" stroke-width="1.2"/><path d="M1 2.8 L6 6.6 L11 2.8" fill="none" stroke="var(--brand-pink)" stroke-width="1.2"/></svg>
          <span>hi@glimora-example.com</span>
        </li>
        <li>
          <svg class="contact-icon" viewBox="0 0 12 12"><circle cx="6" cy="6" r="5" fill="none" stroke="var(--brand-pink)" stroke-width="1.2"/><ellipse cx="6" cy="6" rx="2.2" ry="5" fill="none" stroke="var(--brand-pink)" stroke-width="1"/><path d="M1 6 H11" stroke="var(--brand-pink)" stroke-width="1"/></svg>
          <span>www.glimora-example.com</span>
        </li>
      </ul>
    </div>

    <div class="bottom-band" role="img" aria-label="Decorative pink and plum wave band along the bottom edge"></div>
  </section>
</body>
</html>
```